Borvik Media - Amazing Homepage

We would like to build an amazing homepage for our site. We will need it built in HTM5, so it works across devices and would like it to parallax scroll , so it looks amazing.
We are a digital media agency, that has recently launched. Our old site is self build through one of the standard web build sites. We will be hosting our new site independently.
This is our old site - www.borvik-media.example
The new site only really needs one scrolling page to explain what we do and have our contact details at the bottom.
We have a place to host it, once designed. So we can share with the final design for you to upload.
Attached are:
Brief
Logos and artwork
Our PowerPoint template to give you an idea of colours

```html
<!DOCTYPE html>
<html lang="en">
<head>
<meta charset="utf-8">
<title>Borvik Media – Homepage</title>
<link href="https://fonts.googleapis.com/css2?family=Mulish:wght@400;600;700&display=swap" rel="stylesheet">
<style>
  :root {
    --gold: #d4a734;
    --gold-text: #c99a2c;
    --charcoal: #333333;
    --charcoal-deep: #2a2a2a;
    --footer: #232323;
    --ink: #1e1e1e;
    --client-ink: #555555;
    --grey-icon: #6f6f6f;
    --pale: #e9e9e9;
    --white: #ffffff;
  }
  * { box-sizing: border-box; margin: 0; padding: 0; }
  html, body { width: 1200px; height: 3651px; overflow: hidden; }
  body { font-family: "Mulish", sans-serif; color: var(--ink); background: var(--white); position: relative; }
  section, header, footer { position: absolute; left: 0; width: 1200px; }
  .centered { text-align: center; }
  .caps { text-transform: uppercase; letter-spacing: 0.5px; }

  .site-header { top: 0; height: 102px; background: #f4f4f4; }
  .brand { position: absolute; left: 70px; top: 28px; display: flex; align-items: center; gap: 14px; }
  .brand-dot { width: 40px; height: 40px; border: 3px solid var(--gold); border-radius: 50%; }
  .brand-name { font-size: 34px; font-weight: 600; color: var(--gold); letter-spacing: 2px; }
  .main-nav { position: absolute; right: 68px; top: 42px; display: flex; gap: 44px; font-size: 13px; font-weight: 600; }
  .main-nav a { color: var(--ink); text-decoration: none; }
  .main-nav a.login { color: var(--gold); }

  .hero { top: 102px; height: 450px; }
  .hero-photo { position: absolute; inset: 0; background: radial-gradient(ellipse at 45% 40%, #dff3ff 0%, #7cc5ec 35%, #2f86c6 70%, #1a5f9c 100%); }
  .hero-title { position: absolute; top: 150px; width: 100%; font-size: 42px; font-weight: 700; line-height: 1.12; color: #111; }

  .scroll-cue { position: absolute; left: 576px; width: 48px; height: 48px; }

  .band-dark { top: 552px; height: 86px; background: var(--charcoal); color: var(--white); }
  .band-dark h2 { font-size: 25px; font-weight: 600; line-height: 86px; }

  .clarity { top: 638px; height: 379px; background: var(--gold); color: var(--charcoal-deep); }
  .clarity-list { position: absolute; top: 38px; width: 100%; list-style: none; font-size: 14px; line-height: 2.05; color: #3a2f12; }
  .clarity-motto { position: absolute; top: 214px; width: 100%; font-size: 18px; line-height: 1.6; color: #2a2414; }

  .real-money { top: 1017px; height: 512px; background: var(--white); }
  .real-money h2 { position: absolute; top: 54px; width: 100%; font-size: 23px; font-weight: 600; line-height: 1.35; }
  .tile-label { position: absolute; top: 146px; font-size: 15px; font-weight: 600; color: var(--gold-text); width: 300px; text-align: center; }
  .tile-image { position: absolute; }
  .marbles { left: 146px; top: 212px; width: 450px; height: 160px; background: linear-gradient(90deg, #2c58b8, #e6a83b 30%, #c43a2a 55%, #3aa35a 75%, #d88a2f); border-radius: 80px; opacity: .85; }
  .footballs { left: 742px; top: 188px; width: 330px; height: 200px; background: radial-gradient(ellipse at 60% 55%, #f4f4f4 0%, #bdbdbd 45%, #d63a3a 70%, #ffffff 90%); border-radius: 20px; }

  .coup { top: 1529px; height: 606px; background: var(--gold); }
  .coup h2 { position: absolute; top: 48px; width: 100%; font-size: 22px; font-weight: 600; color: var(--white); line-height: 1.55; }
  .soapbox-art { position: absolute; left: 450px; top: 164px; width: 305px; height: 340px; background: linear-gradient(180deg, #9bc6e6 0%, #6a94c4 55%, #c63a34 80%, #b42a28 100%); border-radius: 12px; }

  .quiet-coup { top: 2135px; height: 226px; background: linear-gradient(100deg, #1c1c1c, #3b3d40 45%, #222 100%); }
  .quiet-coup h2 { position: absolute; top: 68px; width: 100%; font-size: 32px; font-weight: 600; color: var(--white); }

  .growth { top: 2361px; height: 487px; background: var(--white); }
  .growth h2 { position: absolute; top: 56px; width: 100%; font-size: 22px; font-weight: 700; color: var(--gold-text); line-height: 1.4; }
  .growth .lede { position: absolute; top: 125px; width: 100%; font-size: 17px; }
  .service { position: absolute; top: 192px; width: 170px; text-align: center; }
  .service svg { width: 110px; height: 110px; display: block; margin: 0 auto; }
  .service p { margin-top: 20px; font-size: 15px; font-weight: 600; color: var(--gold-text); line-height: 1.3; }

  .results { top: 2848px; height: 287px; background: var(--pale); }
  .results h2 { position: absolute; top: 40px; width: 100%; font-size: 21px; font-weight: 600; line-height: 1.5; }
  .results .brand { left: 480px; top: 132px; }

  .clients { top: 3135px; height: 183px; background: var(--white); }
  .clients h2 { position: absolute; top: 30px; width: 100%; font-size: 22px; font-weight: 600; }
  .client { position: absolute; top: 100px; transform: translateX(-50%); font-size: 30px; font-weight: 600; color: var(--client-ink); white-space: nowrap; }

  .contact { top: 3318px; height: 255px; background: var(--charcoal); color: var(--white); }
  .contact h2 { position: absolute; top: 38px; width: 100%; font-size: 21px; font-weight: 600; line-height: 1.4; }
  .contact .label { position: absolute; width: 100%; font-size: 15px; color: var(--gold); }
  .contact .detail { position: absolute; width: 100%; font-size: 15px; }

  .site-footer { top: 3573px; height: 78px; background: var(--footer); color: #8a8a8a; }
  .copyright { position: absolute; left: 74px; top: 31px; font-size: 12px; }
  .copyright span { color: var(--gold); }
  .social { position: absolute; right: 72px; top: 24px; display: flex; gap: 8px; }
  .social i { width: 28px; height: 28px; border-radius: 50%; background: #8f8f8f; display: block; }
</style>
</head>
<body>

<header class="site-header">
  <div class="brand"><div class="brand-dot"></div><div class="brand-name">BORVIK</div></div>
  <nav class="main-nav">
    <a href="#">HOME</a><a href="#">TECH</a><a href="#">TEAM</a><a href="#">CONTACT</a><a href="#">BLOG</a><a class="login" href="#">LOGIN</a>
  </nav>
</header>

<section class="hero">
  <div class="hero-photo" role="img" aria-label="Hand touching a glowing digital interface with marketing icons"></div>
  <h1 class="hero-title centered caps">Got the feeling your digital marketing<br>just isn’t quite ‘there’?</h1>
  <svg class="scroll-cue" style="top:373px" viewBox="0 0 48 48"><circle cx="24" cy="24" r="21" fill="none" stroke="#1e1e1e" stroke-width="3"/><path d="M14 18h20L24 32z" fill="#1e1e1e"/></svg>
</section>

<section class="band-dark centered"><h2 class="caps">We keep fighting to give you clarity by:</h2></section>

<section class="clarity centered">
  <ul class="clarity-list">
    <li>Creating a singular view of your digital eco system.</li>
    <li>Reviewing how and why your money is being spent where it is.</li>
    <li>Profiling your customers. Who doesn’t have 1000’s of different customers with different<br>motivations, interests and value to the brand?</li>
    <li>Finding the best digital channels to communicate with them.</li>
  </ul>
  <p class="clarity-motto">Because everything is changing every day…exciting isn’t it!<br>Never stop, never settle, always improve.&nbsp; Be amazing.</p>
  <svg class="scroll-cue" style="top:304px" viewBox="0 0 48 48"><circle cx="24" cy="24" r="21" fill="none" stroke="#2a2a2a" stroke-width="3"/><path d="M14 18h20L24 32z" fill="#2a2a2a"/></svg>
</section>

<section class="real-money">
  <h2 class="centered caps">Every client deserves amazing work, regardless of the brand<br>it’s all real money</h2>
  <p class="tile-label caps" style="left:221px">Image of marbles</p>
  <p class="tile-label caps" style="left:757px">Football stickers</p>
  <div class="tile-image marbles" role="img" aria-label="Row of coloured glass marbles"></div>
  <div class="tile-image footballs" role="img" aria-label="Footballs flying over a red swoosh"></div>
  <svg class="scroll-cue" style="top:432px" viewBox="0 0 48 48"><circle cx="24" cy="24" r="21" fill="none" stroke="#1e1e1e" stroke-width="3"/><path d="M14 18h20L24 32z" fill="#1e1e1e"/></svg>
</section>

<section class="coup">
  <h2 class="centered caps">It’s time to start a coup…there are too many large agency networks, too few<br>agencies being transparent, too many putting quality of<br>work second to income</h2>
  <div class="soapbox-art" role="img" aria-label="Cartoon of a man shouting through a megaphone on a red soapbox"></div>
  <svg class="scroll-cue" style="top:535px" viewBox="0 0 48 48"><circle cx="24" cy="24" r="21" fill="none" stroke="#2a2a2a" stroke-width="3"/><path d="M14 18h20L24 32z" fill="#2a2a2a"/></svg>
</section>

<section class="quiet-coup" role="img" aria-label="Dark photo of hands working on a tablet with charts">
  <h2 class="centered caps">Well, a very quiet coup.</h2>
  <svg class="scroll-cue" style="top:153px" viewBox="0 0 48 48"><circle cx="24" cy="24" r="21" fill="none" stroke="#d4a734" stroke-width="3"/><path d="M14 18h20L24 32z" fill="#d4a734"/></svg>
</section>

<section class="growth">
  <h2 class="centered caps">We’ve yet to come across a client that wants to shrink…<br>making us specialists in delivering growth!</h2>
  <p class="lede centered">We’ve been optimising our digital knowledge for over 20 years and we genuinely know what we are talking about</p>

  <div class="service" style="left:61px">
    <svg viewBox="0 0 110 110"><rect x="8" y="14" width="94" height="64" rx="4" fill="none" stroke="#6f6f6f" stroke-width="6"/><rect x="40" y="80" width="30" height="10" fill="#6f6f6f"/><rect x="28" y="90" width="54" height="6" fill="#6f6f6f"/><text x="55" y="56" text-anchor="middle" font-family="Mulish, sans-serif" font-weight="700" font-size="24" fill="#6f6f6f">PPC</text></svg>
    <p class="caps">PPC</p>
  </div>
  <div class="service" style="left:244px">
    <svg viewBox="0 0 110 110"><circle cx="55" cy="55" r="48" fill="#6f6f6f"/><circle cx="55" cy="55" r="38" fill="#fff"/><rect x="33" y="62" width="9" height="16" fill="#6f6f6f"/><rect x="47" y="52" width="9" height="26" fill="#6f6f6f"/><rect x="61" y="42" width="9" height="36" fill="#6f6f6f"/><path d="M30 56 L62 30" stroke="#6f6f6f" stroke-width="4"/><path d="M56 26h12v12z" fill="#6f6f6f"/></svg>
    <p class="caps">SEO</p>
  </div>
  <div class="service" style="left:426px">
    <svg viewBox="0 0 110 110"><rect x="16" y="8" width="78" height="94" rx="8" fill="none" stroke="#6f6f6f" stroke-width="6"/><rect x="30" y="24" width="50" height="6" fill="#6f6f6f"/><rect x="30" y="38" width="50" height="6" fill="#6f6f6f"/><rect x="30" y="52" width="34" height="6" fill="#6f6f6f"/><circle cx="55" cy="90" r="4" fill="#6f6f6f"/></svg>
    <p class="caps">Display</p>
  </div>
  <div class="service" style="left:604px">
    <svg viewBox="0 0 110 110"><circle cx="36" cy="40" r="14" fill="#6f6f6f"/><path d="M10 92c0-24 12-34 26-34s26 10 26 34z" fill="#6f6f6f"/><circle cx="66" cy="46" r="12" fill="#8a8a8a"/><path d="M44 94c0-20 10-30 22-30s22 10 22 30z" fill="#8a8a8a"/><circle cx="90" cy="22" r="14" fill="#6f6f6f"/><text x="90" y="29" text-anchor="middle" font-family="Mulish, sans-serif" font-weight="700" font-size="18" fill="#fff">$</text></svg>
    <p class="caps">Paid Social</p>
  </div>
  <div class="service" style="left:784px">
    <svg viewBox="0 0 110 110"><ellipse cx="55" cy="16" rx="30" ry="9" fill="#6f6f6f"/><rect x="25" y="16" width="60" height="14" fill="#6f6f6f"/><rect x="25" y="34" width="60" height="14" fill="#6f6f6f"/><rect x="25" y="52" width="60" height="14" fill="#6f6f6f"/><rect x="52" y="66" width="6" height="20" fill="#6f6f6f"/><rect x="20" y="86" width="70" height="6" fill="#6f6f6f"/><circle cx="55" cy="89" r="8" fill="#6f6f6f"/></svg>
    <p class="caps">Data<br>Management</p>
  </div>
  <div class="service" style="left:966px">
    <svg viewBox="0 0 110 110"><rect x="18" y="8" width="68" height="92" fill="none" stroke="#6f6f6f" stroke-width="6"/><rect x="30" y="24" width="36" height="5" fill="#6f6f6f"/><rect x="30" y="38" width="44" height="5" fill="#6f6f6f"/><rect x="30" y="52" width="44" height="5" fill="#6f6f6f"/><rect x="30" y="66" width="30" height="5" fill="#6f6f6f"/><path d="M96 20 L68 80 L62 88 L64 78 L92 18z" fill="#6f6f6f"/></svg>
    <p class="caps">Attribution</p>
  </div>
  <svg class="scroll-cue" style="top:390px" viewBox="0 0 48 48"><circle cx="24" cy="24" r="21" fill="none" stroke="#1e1e1e" stroke-width="3"/><path d="M14 18h20L24 32z" fill="#1e1e1e"/></svg>
</section>

<section class="results">
  <h2 class="centered caps">Happily, we smash it for all our clients, with an average of 35% improvement in<br>performance within the first quarter of working with us</h2>
  <div class="brand"><div class="brand-dot" style="width:70px;height:70px"></div><div class="brand-name" style="font-size:38px">BORVIK</div></div>
</section>

<section class="clients">
  <h2 class="centered caps">Clients</h2>
  <div class="client" style="left:158px">Lantern Stage</div>
  <div class="client" style="left:365px">Perch</div>
  <div class="client" style="left:577px">Hollis</div>
  <div class="client" style="left:800px">Calmera</div>
  <div class="client" style="left:1047px">Velora</div>
</section>

<section class="contact centered">
  <h2 class="caps">If you are still reading our rant then<br>get in touch / follow us / let’s go for a coffee</h2>
  <p class="label caps" style="top:120px">Address:</p>
  <p class="detail" style="top:148px">14 Marlow Court, London, N4 2QT</p>
  <p class="label caps" style="top:185px">Contact:</p>
  <p class="detail" style="top:213px">contact@borvik-media.example</p>
</section>

<footer class="site-footer">
  <p class="copyright">Copyright ©2014. <span>Borvik Media</span>. All Right Reserved</p>
  <div class="social" role="img" aria-label="Social media links"><i></i><i></i><i></i><i></i><i></i></div>
</footer>

</body>
</html>
```